New Business Card Design Project LORVANTI-Italy

we are LORVANTI-Italy
our company in the market for 3 years we are luxury cosmetic company and its about time for a facelift :)
i will like to have elegant luxurious and unique business card
that will give the person that get it a unique, luxurious and elegant impression
I'm VERY OPEN FOR NEW IDEAS , even duo i add a few files of things that i see on line and i like them

i add my logo as well
my website is LORVANTI.COM
(if you would like to see the main style that we have)

Target Market(s)

adult that have money :)

Industry/Entity Type

Business

Contact Information for Business Card

Name - Dario Lorvanti
Position - CEO and CO Founder
address - 4817 E Halvern
telephone - 555-384-1926
email - dario@lorvanti.com
fax - 555-384-1926
website - LORVANTI.COM

Colors
000000
959595
fbee3e
ffffff

Requirements
Must have
• big logo in GOLD color
• elegant look
• impressive
Nice to have
• not must but maybe classy pattern background
• not must but maybe emblem
• maybe clear plastic business card
Should not have
• colors
• images

```html
<!DOCTYPE html>
<html lang="en">
<head>
<meta charset="utf-8">
<title>LORVANTI Italy – Business Card</title>
<link href="https://fonts.googleapis.com/css2?family=Roboto:wght@400;500;700&display=swap" rel="stylesheet">
<style>
  :root {
    --backdrop: #2a2623;
    --card: #15171a;
    --card-edge: #0c0d0f;
    --gold: #d4a72c;
    --gold-light: #f0c94a;
    --white: #f4f4f4;
    --grey: #959595;
  }
  * { margin: 0; padding: 0; box-sizing: border-box; }
  html, body {
    width: 1200px; height: 769px; overflow: hidden;
    background: var(--backdrop);
    font-family: "Roboto", Arial, sans-serif;
  }
  .stage {
    position: relative; width: 1200px; height: 769px;
    display: flex; align-items: center; justify-content: center; gap: 60px;
  }
  .card {
    position: relative; width: 520px; height: 297px;
    background: linear-gradient(160deg, #1b1d21 0%, var(--card) 60%, var(--card-edge) 100%);
    border-radius: 3px;
    box-shadow: 0 18px 40px rgba(0,0,0,.55);
  }

  /* Contact side */
  .person { position: absolute; left: 44px; bottom: 52px; }
  .person-name {
    color: var(--gold); font-weight: 700; font-size: 22px; letter-spacing: .3px;
    padding-bottom: 4px; border-bottom: 2px solid var(--gold); display: inline-block;
  }
  .person-role { color: var(--white); font-size: 15px; margin-top: 6px; }

  .contact { position: absolute; left: 318px; top: 96px; list-style: none; }
  .contact li {
    display: flex; align-items: center; gap: 8px;
    color: var(--white); font-size: 13px; line-height: 21px;
  }
  .contact .address { padding-left: 0; }
  .contact .icon { width: 13px; height: 13px; fill: var(--gold); flex: none; }
  .contact .spacer { width: 13px; flex: none; }

  /* Brand side */
  .brand {
    position: absolute; inset: 0;
    display: flex; flex-direction: column; align-items: center; justify-content: center;
    gap: 14px;
  }
  .brand-dot {
    width: 78px; height: 78px; border-radius: 50%;
    border: 3px solid var(--gold);
  }
  .brand-name {
    color: var(--gold); font-weight: 500; font-size: 40px; letter-spacing: 4px;
  }
  .brand-country {
    color: var(--gold); font-weight: 500; font-size: 13px; letter-spacing: 3px;
    margin-top: -10px;
  }
</style>
</head>
<body>
<main class="stage">

  <section class="card card-contact" aria-label="Business card – contact side">
    <div class="person">
      <div class="person-name">DARIO LORVANTI</div>
      <div class="person-role">CEO &amp; CO Founder</div>
    </div>
    <ul class="contact">
      <li class="address"><span class="spacer"></span>4817 E Halvern</li>
      <li><span class="spacer"></span>555-384-1926</li>
      <li>
        <svg class="icon" viewBox="0 0 24 24" aria-hidden="true"><path d="M6.6 10.8a15.1 15.1 0 0 0 6.6 6.6l2.2-2.2c.3-.3.7-.4 1-.2 1.1.4 2.3.6 3.6.6.6 0 1 .4 1 1V20c0 .6-.4 1-1 1A17 17 0 0 1 3 4c0-.6.4-1 1-1h3.5c.6 0 1 .4 1 1 0 1.3.2 2.5.6 3.6.1.3 0 .7-.2 1z"/></svg>
        555-384-1926
      </li>
      <li>
        <svg class="icon" viewBox="0 0 24 24" aria-hidden="true"><path d="M6 3h12v5H6zM3 9h18v8h-3v4H6v-4H3zm5 6v4h8v-4z"/></svg>
        555-384-1926
      </li>
      <li>
        <svg class="icon" viewBox="0 0 24 24" aria-hidden="true"><path d="M2 5h20v14H2zm2 2v.5l8 5 8-5V7z"/></svg>
        dario@lorvanti.com
      </li>
      <li>
        <svg class="icon" viewBox="0 0 24 24" aria-hidden="true"><circle cx="12" cy="12" r="10"/><path d="M2 12h20M12 2c3 3 3 17 0 20M12 2c-3 3-3 17 0 20" stroke="#15171a" stroke-width="1.5" fill="none"/></svg>
        LORVANTI.COM
      </li>
    </ul>
  </section>

  <section class="card card-brand" aria-label="Business card – brand side">
    <div class="brand">
      <div class="brand-dot" aria-hidden="true"></div>
      <div class="brand-name">LORVANTI</div>
      <div class="brand-country">ITALY</div>
    </div>
  </section>

</main>
</body>
</html>
```